FLYER DESIGN FOR INTERNATIONAL CONSULTANCY FINANCIAL AND LEGAL SERVICES

I would like high quality flyer designed that I can share via WhatsAPP that should include a clickable link allowing people link to my Calendly calender and clickable telephone number that allows them to call

I've added all the necessary text on the attached word document and my profile picture.

We need excellent images, type setting aligned with the KWF brand.

www.kwfwillsandtrusts.co.uk

Target Market(s)

PROFESSIONALS / HIGH NET WORTH / ULTRA HIGH NET WORTH

Font styles to use
Sans Serif

Requirements
Must have
• ELEGANCE
AUTHORITY
INTEGRITY
Please see existing branding on existing website http://kwfwillsandtrusts.co.uk/
Excellent relevant imagery
Nice to have
• Clickable calendly url
Clickable phone number
IF THIS IS NOT POSSIBLE LET ME KNOW

```html
<!DOCTYPE html>
<html lang="en">
<head>
<meta charset="utf-8">
<title>KWF Estate Planning – Flyer</title>
<link rel="stylesheet" href="https://fonts.googleapis.com/css2?family=Open+Sans:ital,wght@0,300;0,400;0,600;0,700;1,400;1,600&display=swap">
<style>
:root{
  --orange:#e0694f;
  --blue:#2c5f8f;
  --ink:#1b1b1b;
  --dark:#151515;
  --soft:#f2f2f2;
  --rule:#c9c9c9;
  --stage:#b4b4b4;
  --white:#ffffff;
}
*{margin:0;padding:0;box-sizing:border-box}
html,body{width:1200px;height:612px;overflow:hidden;background:var(--stage);font-family:"Open Sans",Arial,sans-serif;color:var(--ink)}
.flyer{position:absolute;left:395px;top:16px;width:410px;height:580px;background:var(--white);overflow:hidden;box-shadow:0 2px 8px rgba(0,0,0,.25)}
.abs{position:absolute}

/* header */
.hero{left:0;top:0;width:410px;height:208px;background:linear-gradient(90deg,#0e0f11 0%,#1d2126 38%,#4b525a 62%,#6e6f70 80%,#3b4148 100%)}
.brand{left:18px;top:22px;display:flex;align-items:center;gap:6px;color:var(--blue);font-weight:600}
.brand-mark{width:14px;height:14px;border-radius:50%;background:var(--blue)}
.brand-name{font-size:26px;line-height:1;letter-spacing:.5px}
.brand-sub{font-size:11px;line-height:1.05;font-weight:600}
.offer{left:20px;top:80px;color:var(--orange);font-size:14px;font-weight:400;line-height:1}
.headline{left:20px;top:98px;color:var(--white);font-weight:700;font-size:16.5px;line-height:19.5px;text-transform:uppercase}
.tagline{left:20px;top:162px;color:var(--orange);font-size:12.5px;line-height:16px}

/* services */
.advise{left:22px;top:215px;width:170px}
.advise h2{color:var(--orange);font-size:9.5px;font-weight:700;margin-bottom:4px}
.advise ul{list-style:none}
.advise li{position:relative;padding-left:11px;font-size:6.3px;line-height:7.6px;margin-bottom:2.1px}
.advise li svg{position:absolute;left:0;top:1px;width:6.5px;height:6.5px}
.clients{left:22px;top:349px;font-size:8.5px;font-weight:600;line-height:10.5px}
.clients span{color:var(--orange);display:block}
.note{left:22px;top:377px;width:165px;font-size:5.3px;font-style:italic;line-height:6.8px;text-align:justify}
.divider{left:201px;top:215px;width:1px;height:178px;background:var(--rule)}

/* testimonials */
.quote{left:219px;width:174px;border:1px dashed var(--rule);border-radius:6px;padding:12px 6px 4px;font-size:5.1px;font-style:italic;line-height:6.6px;text-align:justify}
.quote .by{text-align:center;margin-top:5px;font-size:5.6px}
.quote .by b{color:var(--orange);font-weight:600;font-size:6.4px}
.q1{top:227px;height:67px}
.q2{top:315px;height:69px;padding-top:12px}
.qmark{width:24px;height:16px;background:var(--white);text-align:center;color:#b9b9b9;font-family:Georgia,serif;font-weight:700;font-size:30px;line-height:28px}
.more{left:219px;top:389px;width:174px;text-align:center;font-size:5.3px;font-style:italic}

/* profile */
.profile{left:0;top:403px;width:410px;height:137px;background:var(--soft)}
.portrait{left:27px;top:413px;width:114px;height:114px;border-radius:50%;background:radial-gradient(circle at 50% 45%,#b48c76 0%,#6a6e78 45%,#3a4252 100%);border:2px solid #222}
.person{left:156px;top:415px;width:236px}
.person h3{color:var(--orange);font-size:11.3px;font-weight:700;line-height:13px}
.person .cred{font-size:6.9px;font-style:italic;font-weight:600;margin-top:2px}
.person .bio{font-size:5.5px;line-height:6.9px;text-align:justify;margin-top:5px}
.person .contact{font-size:5.9px;line-height:7.6px;margin-top:7px}
.person .contact a{color:var(--ink);font-weight:700;text-decoration:none}
.phone{display:inline-block;width:6px;height:6px;vertical-align:-1px;margin-right:1px}
.book{left:156px;top:516px;width:221px;height:15px;border-radius:8px;background:var(--orange);color:var(--white);font-size:7.6px;font-weight:700;text-align:center;line-height:15px;text-decoration:none;letter-spacing:.2px}

/* footer */
.footer{left:0;top:540px;width:410px;height:40px;background:var(--dark)}
.footer-band{left:0;top:540px;width:200px;height:40px}
.company{left:22px;top:545px;color:var(--white);line-height:9px}
.company b{font-size:9px;font-weight:700;display:block;margin-bottom:2px}
.company span{font-size:7px;display:block}
.globe{left:202px;top:552px;width:14px;height:14px}
.site{left:229px;top:548px;color:var(--white);font-size:7px;font-weight:600;line-height:12px}
.site a{color:var(--white);font-size:8.6px;font-weight:700;text-decoration:none;display:block}
</style>
</head>
<body>
<main class="flyer">

  <section class="hero abs" role="img" aria-label="Photograph of two business professionals in suits walking through an office, one holding a tablet and folder"></section>

  <div class="brand abs">
    <span class="brand-mark"></span>
    <span class="brand-name">KWF</span>
    <span class="brand-sub">Estate<br>Planning</span>
  </div>

  <p class="offer abs">WE OFFER*</p>
  <h1 class="headline abs">High Quality<br>Discreet Consultancy<br>Services</h1>
  <p class="tagline abs">For Private Individuals &amp;<br>Families with Complex Affairs.</p>

  <section class="advise abs">
    <h2>WE ADVISE ON:</h2>
    <ul>
      <li><svg viewBox="0 0 10 10"><rect x=".6" y="1.6" width="7.8" height="7.8" fill="none" stroke="#e0694f" stroke-width="1"/><path d="M2.4 5.2l2 2L9.4.8" fill="none" stroke="#e0694f" stroke-width="1.2"/></svg>Bloodline planning; specialist wills and trust funds</li>
      <li><svg viewBox="0 0 10 10"><rect x=".6" y="1.6" width="7.8" height="7.8" fill="none" stroke="#e0694f" stroke-width="1"/><path d="M2.4 5.2l2 2L9.4.8" fill="none" stroke="#e0694f" stroke-width="1.2"/></svg>Business Succession Planning</li>
      <li><svg viewBox="0 0 10 10"><rect x=".6" y="1.6" width="7.8" height="7.8" fill="none" stroke="#e0694f" stroke-width="1"/><path d="M2.4 5.2l2 2L9.4.8" fill="none" stroke="#e0694f" stroke-width="1.2"/></svg>Asset Protection Planning; protection against third party threats</li>
      <li><svg viewBox="0 0 10 10"><rect x=".6" y="1.6" width="7.8" height="7.8" fill="none" stroke="#e0694f" stroke-width="1"/><path d="M2.4 5.2l2 2L9.4.8" fill="none" stroke="#e0694f" stroke-width="1.2"/></svg>Lasting Powers of Attorney</li>
      <li><svg viewBox="0 0 10 10"><rect x=".6" y="1.6" width="7.8" height="7.8" fill="none" stroke="#e0694f" stroke-width="1"/><path d="M2.4 5.2l2 2L9.4.8" fill="none" stroke="#e0694f" stroke-width="1.2"/></svg>Inheritance Tax Planning</li>
      <li><svg viewBox="0 0 10 10"><rect x=".6" y="1.6" width="7.8" height="7.8" fill="none" stroke="#e0694f" stroke-width="1"/><path d="M2.4 5.2l2 2L9.4.8" fill="none" stroke="#e0694f" stroke-width="1.2"/></svg>Capital Gains Tax Planning</li>
      <li><svg viewBox="0 0 10 10"><rect x=".6" y="1.6" width="7.8" height="7.8" fill="none" stroke="#e0694f" stroke-width="1"/><path d="M2.4 5.2l2 2L9.4.8" fill="none" stroke="#e0694f" stroke-width="1.2"/></svg>Property Portfolio structuring</li>
      <li><svg viewBox="0 0 10 10"><rect x=".6" y="1.6" width="7.8" height="7.8" fill="none" stroke="#e0694f" stroke-width="1"/><path d="M2.4 5.2l2 2L9.4.8" fill="none" stroke="#e0694f" stroke-width="1.2"/></svg>Global Wealth Management advice; on a no-commission and no exit penalty basis</li>
      <li><svg viewBox="0 0 10 10"><rect x=".6" y="1.6" width="7.8" height="7.8" fill="none" stroke="#e0694f" stroke-width="1"/><path d="M2.4 5.2l2 2L9.4.8" fill="none" stroke="#e0694f" stroke-width="1.2"/></svg>ESG and Ethical Investments</li>
      <li><svg viewBox="0 0 10 10"><rect x=".6" y="1.6" width="7.8" height="7.8" fill="none" stroke="#e0694f" stroke-width="1"/><path d="M2.4 5.2l2 2L9.4.8" fill="none" stroke="#e0694f" stroke-width="1.2"/></svg>Second Passport and Second Residency options</li>
    </ul>
  </section>

  <p class="clients abs">We have clients across the <span>UK, GREECE, MIDDLE EAST, AND ASIA.</span></p>
  <p class="note abs">*Some services may be provided in conjunction with our associate partner firms to ensure a joined up approach.</p>

  <div class="divider abs"></div>

  <blockquote class="quote q1 abs">
    Very professional interaction, first class service, informative and a global view on the subject. I would highly recommend Daniel Harcourt and his team who are well informed and highly efficient in their field. Thank you
    <p class="by"><b>Martin</b> <i>(Director, and Founder of a global marine engineering and maintenance company)</i></p>
  </blockquote>
  <div class="qmark abs" style="left:294px;top:219px">&ldquo;</div>

  <blockquote class="quote q2 abs">
    Daniel is well qualified and knowledgable with regard to Trusts and Estate Planning. He is able to identify sympathetically with clients and uses his know-how in practical examples. Clients like him – he is straight forward, empathetic and patient. Behind the scenes he is meticulous and efficient. I am very pleased to have made his acquaintance and would have no hesitation in recommending him to those who want a truly professional approach for their clients.
    <p class="by"><b>Richard</b> &nbsp;– former Associate Director at Northgate Bank</p>
  </blockquote>
  <div class="qmark abs" style="left:294px;top:307px">&ldquo;</div>

  <p class="more abs">See more independent reviews on ReviewHub</p>

  <section class="profile abs"></section>
  <div class="portrait abs" role="img" aria-label="Circular portrait photograph of the adviser in a suit and red tie"></div>

  <section class="person abs">
    <h3>DANIEL HARCOURT</h3>
    <p class="cred">MA DipFA PETR Associate Member of GEA</p>
    <p class="bio">is an international wealth manager who holds dual accreditations across wealth management and trust planning. He advises high-net worth (HNW) individuals on how best to protect their family and structure their estate for the benefit of successive generations. Daniel is also an associate member of the Guild of Estate Advisers (GEA). His experience also includes adjudicating on c300 complex pension complaints in the UK for the UK's National Finance Ombudsman.</p>
    <p class="contact">Contact Daniel Harcourt directly on
      <svg class="phone" viewBox="0 0 10 10"><circle cx="5" cy="5" r="5" fill="#e0694f"/><path d="M3.3 2.6l1 1-.6.7c.4.9 1 1.5 1.9 1.9l.7-.6 1 1-.7.8c-2 0-4-2-4-4z" fill="#fff"/></svg><a href="tel:+44700900123">+44700 900123</a> or<br>book a consultancy slot via his booking link:</p>
  </section>
  <a class="book abs" href="https://booking.kwfwillsandtrusts.co.uk">HTTPS://BOOKING.KWFWILLSANDTRUSTS.CO.UK</a>

  <footer>
    <div class="footer abs"></div>
    <svg class="footer-band abs" viewBox="0 0 200 40" preserveAspectRatio="none"><polygon points="0,0 190,0 200,40 0,40" fill="#e0694f"/></svg>
    <p class="company abs"><b>KWF Estate Planning Ltd</b><span>12 Meridian Court, Fleet Lane,</span><span>City of London, EC4A 9XY</span></p>
    <svg class="globe abs" viewBox="0 0 20 20"><circle cx="10" cy="10" r="9.5" fill="#e0694f"/><g fill="none" stroke="#fff" stroke-width="1"><circle cx="10" cy="10" r="5.5"/><ellipse cx="10" cy="10" rx="2.4" ry="5.5"/><path d="M4.5 10h11M5.3 7.3h9.4M5.3 12.7h9.4"/></g></svg>
    <p class="site abs">You can also visit our website at:<a href="http://kwfwillsandtrusts.co.uk/">WWW.KWFWILLSANDTRUSTS.CO.UK</a></p>
  </footer>

</main>
</body>
</html>
```